Stationery Design Task - Stationary, memo and report templates for professional services company

Looking for someone to update stationary design but just as importantly come up with a template for reports and memos for use in our consulting firm. Would also like some brand use guidelines to be able to share with our whole team. We have an existing logo that we like. Need to update with a more contemporary look so that our deliverables to clients look good and professional yet stylish. This is for business to business communications. No need for envelope design. Important to have design for multiple pages, i.e. first page of a report and then 2nd page. Need to use in MS word documents so must be easy to use and replicate. Don't want something overly complex. Clean, fresh looking is best.

Industry/Entity Type

Information Technology

Font styles to use
Sans Serif

Colors
33a6d7
0792cd
85cae6
cee9f5
cedeed
85abd2
3377b5
0455a3

Requirements
Must have
• Clean look but with a little style or pop. Something that can easily be used in word documents. Need to have page styles that have a first page of a report (not a cover page) and then secondary page.
Nice to have
• - Although the dark blue is our primary color. Might be willing to look at some accent color as well.
Should not have
• Not just our logo on the page with a color bar.

```html
<!DOCTYPE html>
<html lang="en">
<head>
<meta charset="utf-8">
<title>Nexora Technology — Letterhead</title>
<link href="https://fonts.googleapis.com/css2?family=Exo+2:wght@700&display=swap" rel="stylesheet">
<style>
  :root {
    --backdrop: #dcdcdc;
    --paper: #ffffff;
    --brand-blue: #0455a3;
    --accent-blue: #0792cd;
    --wave-blue: #d6e8f4;
    --wave-grey: #e2e2e2;
    --edge-grey: #b9b9b9;
    --pattern-grey: #eeeeee;
  }
  html, body {
    margin: 0;
    width: 1200px;
    height: 784px;
    overflow: hidden;
    background: var(--backdrop);
  }
  .canvas {
    position: relative;
    width: 1200px;
    height: 784px;
  }
  .letterhead {
    position: absolute;
    left: 337px;
    top: 20px;
    width: 526px;
    height: 744px;
    background: var(--paper);
    box-shadow: 0 2px 10px rgba(0,0,0,0.12);
    overflow: hidden;
  }
  .letterhead__art {
    position: absolute;
    inset: 0;
  }
  .brand {
    position: absolute;
    left: 96px;
    top: 70px;
    display: flex;
    align-items: center;
    gap: 10px;
    font-family: "Exo 2", sans-serif;
    font-weight: 700;
    font-size: 24px;
    color: var(--brand-blue);
    letter-spacing: 0.5px;
    white-space: nowrap;
  }
  .brand__dot {
    width: 22px;
    height: 22px;
    border-radius: 50%;
    background: var(--brand-blue);
  }
</style>
</head>
<body>
<main class="canvas">
  <section class="letterhead" aria-label="Company letterhead">
    <svg class="letterhead__art" width="526" height="744" viewBox="0 0 526 744" aria-hidden="false">
      <!-- corner accent ticks -->
      <rect class="tick tick--left-blue" x="0" y="16" width="4" height="26" fill="var(--accent-blue)"/>
      <rect class="tick tick--left-grey" x="0" y="44" width="4" height="22" fill="var(--edge-grey)"/>
      <rect class="tick tick--right-blue" x="522" y="16" width="4" height="26" fill="var(--accent-blue)"/>
      <rect class="tick tick--right-grey" x="522" y="44" width="4" height="22" fill="var(--edge-grey)"/>

      <!-- background sphere pattern placeholder -->
      <circle class="sphere-pattern" cx="120" cy="530" r="82" fill="var(--pattern-grey)"
              role="img" aria-label="Faint grey hexagon globe decoration"/>

      <!-- sweeping waves, bottom-left corner -->
      <path class="wave wave--grey" d="M0 560 C 40 650, 150 690, 300 744 L 260 744 C 130 700, 20 660, 0 610 Z" fill="var(--wave-grey)"/>
      <path class="wave wave--blue" d="M0 640 C 60 700, 200 700, 520 744 L 0 744 Z" fill="var(--wave-blue)"/>
      <path class="wave wave--white" d="M0 665 C 80 715, 220 700, 470 744 L 420 744 C 220 712, 80 725, 0 685 Z" fill="var(--paper)"/>

      <!-- bottom edge accent bar -->
      <rect class="edge-bar edge-bar--blue" x="0" y="740" width="290" height="4" fill="var(--accent-blue)"/>
      <rect class="edge-bar edge-bar--grey" x="294" y="740" width="30" height="4" fill="var(--edge-grey)"/>
      <rect class="edge-bar edge-bar--side" x="0" y="560" width="4" height="184" fill="var(--accent-blue)"/>
    </svg>

    <div class="brand">
      <span class="brand__dot" aria-hidden="true"></span>
      <span class="brand__name">Nexora Technology</span>
    </div>
  </section>
</main>
</body>
</html>
```